Bed Company needs business card

Hello, we are a bed company that makes specialized magnets for beds. We are an alternative healing company. I need a modern and upscale business card. Please incorporate my logo for the card.

Accepted file formats are AI, EPS, and Press-Ready PDFS.

Please include all fonts or convert them to outlines regardless of file type.

If you are designing the card in Photoshop the file Must be 1200dpi.

I am open to anything for the business card.  I really like all of your designs and if you want to change the color of the logo, you can.  I will be making the final selection by Friday.  Thank You for all of your designs.  Feel Free to submit different color logos if you want.  

Reason: I will make a decision Final on Friday April 20th. 2012. Good Luck and Thank you all for the designs.

Target Market(s)

My target Market is people, who are looking for alternative healing.

Industry/Entity Type

Business

Requirements
Must have
• My logo must be incorporated. The front card must have

Name
Job Title

Address
Work
Cell
Fax
email
web

Just put in fake info for the card.

The back of the card. I want the logo on the back with color. I just want it to look modern and cool.

```html
<!DOCTYPE html>
<html lang="en">
<head>
<meta charset="utf-8">
<title>Restfield – Business Card</title>
<link href="https://fonts.googleapis.com/css2?family=Open+Sans:wght@400;600;700&display=swap" rel="stylesheet">
<style>
  :root {
    --green-deep: #0d6233;
    --green-bright: #4fb848;
    --green-text: #166b34;
    --ink: #3a3a3a;
    --ink-soft: #444;
    --card: #ffffff;
    --stage-light: #dcdcdc;
    --stage-dark: #b2b2b2;
  }
  * { margin: 0; padding: 0; box-sizing: border-box; }
  html, body { width: 1200px; height: 900px; overflow: hidden; }
  body {
    position: relative;
    background: radial-gradient(ellipse at 40% 40%, var(--stage-light) 0%, var(--stage-dark) 100%);
    font-family: "Open Sans", sans-serif;
    color: var(--ink);
  }
  .card {
    position: absolute;
    top: 291px;
    width: 509px;
    height: 318px;
    background: var(--card);
    box-shadow: 2px 3px 4px rgba(0,0,0,0.35);
    overflow: hidden;
  }
  .card--front { left: 72px; }
  .card--back { left: 625px; width: 508px; }

  .front-panel { position: absolute; left: 0; top: 0; width: 280px; height: 318px; }

  .holder { position: absolute; left: 270px; top: 50px; width: 190px; text-align: center; }
  .holder__name { font-size: 26px; font-weight: 400; color: var(--ink); line-height: 1.2; white-space: nowrap; }
  .holder__title { font-size: 16px; color: var(--green-text); line-height: 1.3; }

  .contacts { position: absolute; left: 287px; top: 134px; font-size: 13px; line-height: 17.5px; color: var(--ink-soft); }
  .contacts__row { display: flex; }
  .contacts__label { width: 34px; }
  .contacts__sep { width: 18px; }

  .online { position: absolute; left: 287px; top: 210px; font-size: 13px; line-height: 18px; }
  .online__mail { color: var(--ink-soft); }
  .online__web { color: var(--green-text); }

  .venue { position: absolute; left: 287px; top: 251px; font-size: 9px; line-height: 13px; color: var(--ink-soft); white-space: nowrap; }

  .brand__mark { position: absolute; left: 72px; top: 96px; width: 64px; height: 64px; background: var(--green-deep); }
  .brand__name {
    position: absolute; left: 139px; top: 152px;
    font-size: 50px; font-weight: 700; color: var(--green-bright); line-height: 1;
  }
  .brand__tagline {
    position: absolute; left: 254px; top: 207px;
    font-size: 15px; letter-spacing: 1.5px; color: var(--green-text); white-space: nowrap;
  }
</style>
</head>
<body>
  <section class="card card--front" aria-label="Front of card">
    <svg class="front-panel" viewBox="0 0 280 318" aria-hidden="true">
      <polygon points="0,0 276,0 270,318 0,318" fill="var(--green-bright)"/>
      <polygon points="0,0 266,0 260,318 0,318" fill="var(--green-deep)"/>
    </svg>

    <div class="holder">
      <div class="holder__name">Alan Harper</div>
      <div class="holder__title">director</div>
    </div>

    <div class="contacts">
      <div class="contacts__row"><span class="contacts__label">tel</span><span class="contacts__sep">:</span><span>(555) 210 4831</span></div>
      <div class="contacts__row"><span class="contacts__label">cell</span><span class="contacts__sep">:</span><span>(555) 210 4832</span></div>
      <div class="contacts__row"><span class="contacts__label">fax</span><span class="contacts__sep">:</span><span>(555) 210 4839</span></div>
    </div>

    <div class="online">
      <div class="online__mail">office@restfieldsleep.com</div>
      <div class="online__web">www.restfield-sleep.com</div>
    </div>

    <div class="venue">
      May 14-17, 2013, Lakeview Hall East,<br>
      Harbor City IL, Booth 208
    </div>
  </section>

  <section class="card card--back" aria-label="Back of card">
    <span class="brand__mark" aria-hidden="true"></span>
    <span class="brand__name">Restfield</span>
    <div class="brand__tagline">Alternative Healing</div>
  </section>
</body>
</html>
```